Car transport business

We need a new business card design. Attached is our old card sample. I would just like to adjust the logo colors (blue and red) to be brighter. I changed my name to the brighter red and the word dispatcher to a brighter blue as an example. But you can adjust those colors further. And then perhaps you can use the same colors for the card design but use your imagination.

As a suggestion so the card stands out I would like to add a clip art of car carrier truck. Attached are examples of that as well

```html
<!DOCTYPE html>
<html lang="en">
<head>
<meta charset="utf-8">
<title>Northlane Haul – Business Card</title>
<link rel="stylesheet" href="https://fonts.googleapis.com/css2?family=Montserrat:wght@400;600;800&display=swap">
<style>
  :root {
    --backdrop: #dcdcdc;
    --card-white: #ffffff;
    --brand-red: #c01d2e;
    --brand-blue: #17598a;
    --card-navy: #165a86;
    --logo-blue: #3ea4ee;
    --tagline-blue: #0f3f63;
  }
  * { margin: 0; padding: 0; box-sizing: border-box; }
  html, body {
    width: 1200px; height: 1200px; overflow: hidden;
    background: var(--backdrop);
    font-family: "Montserrat", Arial, sans-serif;
  }
  .canvas { position: relative; width: 1200px; height: 1200px; }

  .card { position: absolute; left: 207px; width: 786px; height: 449px; }
  .card--front { top: 112px; background: var(--card-white); }
  .card--back { top: 640px; background: var(--card-navy); }

  .identity {
    position: absolute; right: 440px; top: 192px; text-align: right;
  }
  .identity__name {
    font-weight: 600; font-size: 38px; line-height: 1;
    color: var(--brand-red); letter-spacing: 0;
  }
  .identity__role {
    font-weight: 400; font-size: 20px; line-height: 1;
    color: var(--brand-blue); margin-top: 9px; letter-spacing: 0.3px;
  }
  .divider {
    position: absolute; left: 371px; top: 194px; width: 2px; height: 67px;
    background: var(--brand-red);
  }
  .contacts { position: absolute; left: 404px; top: 190px; list-style: none; }
  .contacts__item {
    display: flex; align-items: center; gap: 8px;
    font-size: 20px; line-height: 25px; color: var(--brand-blue);
  }
  .contacts__icon { width: 16px; height: 16px; flex: none; }

  .logo__dot {
    position: absolute; left: 136px; top: 168px;
    width: 76px; height: 76px; border-radius: 50%;
    background: var(--logo-blue);
  }
  .logo__text { position: absolute; left: 215px; top: 231px; }
  .logo__name {
    font-weight: 800; font-size: 37px; line-height: 1;
    color: var(--logo-blue); letter-spacing: 0.5px; white-space: nowrap;
  }
  .logo__tagline {
    font-weight: 400; font-size: 12px; letter-spacing: 3.4px;
    color: var(--tagline-blue); margin-top: 7px; white-space: nowrap;
  }
</style>
</head>
<body>
<main class="canvas">
  <section class="card card--front">
    <div class="identity">
      <div class="identity__name">MILO VAREN</div>
      <div class="identity__role">DISPATCHER</div>
    </div>
    <div class="divider"></div>
    <ul class="contacts">
      <li class="contacts__item">
        <svg class="contacts__icon" viewBox="0 0 16 16"><path d="M4 1.5l2.2 3-1.3 1.6c.8 1.8 2 3.2 3.7 4.3l1.6-1.2 2.8 2.3-1.4 2.3C7.3 13.3 2.8 8.6 2 3z" fill="none" stroke="var(--brand-red)" stroke-width="1.4" stroke-linejoin="round"/></svg>
        <span>312-555-0147</span>
      </li>
      <li class="contacts__item">
        <svg class="contacts__icon" viewBox="0 0 16 16"><rect x="4" y="1" width="8" height="4" fill="var(--brand-red)"/><rect x="1" y="5" width="14" height="6" rx="1.5" fill="var(--brand-red)"/><rect x="4" y="9" width="8" height="6" fill="#fff" stroke="var(--brand-red)" stroke-width="1.4"/></svg>
        <span>312-555-0193</span>
      </li>
      <li class="contacts__item">
        <svg class="contacts__icon" viewBox="0 0 16 16"><rect x="1.5" y="3.5" width="13" height="9" fill="none" stroke="var(--brand-red)" stroke-width="1.4"/><path d="M1.5 3.5L8 9l6.5-5.5" fill="none" stroke="var(--brand-red)" stroke-width="1.4"/></svg>
        <span>northlanehaul@mail.com</span>
      </li>
    </ul>
  </section>

  <section class="card card--back">
    <div class="logo__dot"></div>
    <div class="logo__text">
      <div class="logo__name">NORTHLANE HAUL</div>
      <div class="logo__tagline">YOUR TRUSTED VEHICLE CARRIER TEAM</div>
    </div>
  </section>
</main>
</body>
</html>
```